Half page (a5) ad for a company

I need a design for an ad for a company to be published in a conference catalogue. Please find enclosed the logo for a company. The company is providing health screening services. Ad should be subtle and minimalistic, i.e. logo in the centre and a phrase saying: "Be in charge of your own health" and the website bluefen.co.uk. Also please find enclosed guidlines for colours and fonts to be used.

```html
<!DOCTYPE html>
<html lang="en">
<head>
<meta charset="utf-8">
<title>The Blue Fen Private – Half Page Ad</title>
<link rel="stylesheet" href="https://fonts.googleapis.com/css2?family=Montserrat:ital,wght@0,300;0,400;0,700;1,400&display=swap">
<style>
  :root {
    --paper: #ffffff;
    --frame: #6b6b6b;
    --brand-red: #e3141e;
    --ink-grey: #666666;
    --url-grey: #5a5a5a;
    --photo-top: #3a2a24;
    --photo-mid: #e5404a;
    --photo-low: #d8d8d8;
  }
  * { box-sizing: border-box; margin: 0; padding: 0; }
  html, body { width: 1200px; height: 846px; overflow: hidden; background: var(--paper); }
  .ad {
    position: relative;
    width: 1200px;
    height: 846px;
    background: var(--paper);
    border: 1px solid var(--frame);
    font-family: "Montserrat", sans-serif;
  }
  .runner-photo {
    position: absolute;
    left: 196px;
    top: 76px;
    width: 243px;
    height: 700px;
    border-radius: 120px 120px 60px 60px;
    background: linear-gradient(180deg,
      var(--photo-top) 0%,
      #8a6a5a 22%,
      #1d1d1f 32%,
      #c99a80 40%,
      var(--photo-mid) 45%,
      var(--photo-mid) 82%,
      var(--photo-low) 92%,
      var(--paper) 100%);
    opacity: 0.9;
  }
  .brand-block {
    position: absolute;
    left: 624px;
    width: 400px;
    text-align: center;
  }
  .brand-mark {
    top: 242px;
  }
  .brand-dot {
    display: block;
    margin: 0 auto 50px;
  }
  .brand-name {
    font-weight: 400;
    font-size: 28px;
    color: var(--brand-red);
    letter-spacing: 0.2px;
    line-height: 1.2;
  }
  .brand-name span { display: block; }
  .tagline {
    top: 458px;
    font-size: 23px;
    color: var(--ink-grey);
    letter-spacing: -0.7px;
    white-space: nowrap;
  }
  .tagline .lead { font-weight: 700; }
  .tagline .emph { font-weight: 400; font-style: italic; }
  .website {
    top: 580px;
    font-weight: 300;
    font-size: 19px;
    letter-spacing: 3.2px;
    color: var(--url-grey);
  }
</style>
</head>
<body>
  <main class="ad">
    <div class="runner-photo" role="img" aria-label="Photo of a young woman with curly hair jogging towards the viewer in a black sports top, red leggings and white trainers"></div>

    <div class="brand-block brand-mark">
      <svg class="brand-dot" width="48" height="48" viewBox="0 0 48 48" aria-hidden="true">
        <circle cx="24" cy="24" r="23" fill="var(--brand-red)"/>
      </svg>
      <p class="brand-name"><span>The Blue Fen</span><span>Private</span></p>
    </div>

    <p class="brand-block tagline"><span class="lead">Be in charge of</span> <span class="emph">your own health</span></p>

    <p class="brand-block website">www.bluefen.co.uk</p>
  </main>
</body>
</html>
```